Every Shelf Set Neatly or ESN Organized needs a business card design. ESN Organized is a professi

We need a business card design that is clean, sharp and conveys a sense of organization. I already have a logo.

Target Market(s)

Families (specifically mothers), small business owners, parents, seniors

Industry/Entity Type

Business

Contact Information for Business Card

My website is www.esnorganized-example.com and my Facebook page is http://www.sociallink-example.com/everyshelfsetneatly. The phone number is 418-552-7094 and I want to be listed as Lorna M. Pelham, Owner

Requirements
Must have
• My logo.

```html
<!DOCTYPE html>
<html lang="en">
<head>
<meta charset="utf-8">
<title>Every Shelf Set Neatly – Business Card</title>
<link href="https://fonts.googleapis.com/css2?family=Montserrat:wght@400;500;600&display=swap" rel="stylesheet">
<style>
  :root {
    --backdrop: #262626;
    --card-light: #f1f1f0;
    --card-dark: #000000;
    --accent-blue: #1a7fd4;
    --ink: #141414;
    --text-light: #ffffff;
  }
  * { margin: 0; padding: 0; box-sizing: border-box; }
  html, body {
    width: 1200px;
    height: 840px;
    overflow: hidden;
    background: var(--backdrop);
    font-family: "Montserrat", Arial, sans-serif;
  }
  .card {
    position: absolute;
    left: 384px;
    width: 460px;
    height: 262px;
    overflow: hidden;
  }
  .card-front { top: 121px; background: var(--card-light); }
  .card-back  { top: 442px; background: var(--card-dark); }

  .brand-name {
    position: absolute;
    left: 36px;
    right: 36px;
    top: 116px;
    font-size: 24px;
    font-weight: 500;
    letter-spacing: 2px;
    color: var(--ink);
    white-space: nowrap;
  }

  .divider-line {
    position: absolute;
    left: 76px;
    top: 0;
    bottom: 0;
    width: 2px;
    background: var(--accent-blue);
  }

  .owner {
    position: absolute;
    right: 36px;
    top: 20px;
    text-align: right;
  }
  .owner-name {
    font-size: 18px;
    font-weight: 600;
    color: var(--accent-blue);
    line-height: 1.2;
  }
  .owner-role {
    font-size: 13px;
    font-weight: 400;
    color: var(--text-light);
    letter-spacing: 0.5px;
  }

  .contact-list {
    position: absolute;
    right: 36px;
    top: 189px;
    list-style: none;
  }
  .contact-item {
    display: flex;
    justify-content: flex-end;
    align-items: center;
    gap: 8px;
    height: 17.5px;
    font-size: 13px;
    color: var(--text-light);
  }
  .contact-icon { width: 11px; height: 11px; flex: none; }
</style>
</head>
<body>

<section class="card card-front" aria-label="Card front">
  <div class="brand-name">Every Shelf Set Neatly</div>
</section>

<section class="card card-back" aria-label="Card back">
  <div class="divider-line"></div>

  <div class="owner">
    <div class="owner-name">Lorna M. Pelham</div>
    <div class="owner-role">Owner</div>
  </div>

  <ul class="contact-list">
    <li class="contact-item">
      <span>418-552-7094</span>
      <svg class="contact-icon" viewBox="0 0 24 24" aria-hidden="true">
        <path fill="#1a7fd4" d="M6.6 10.8a15.1 15.1 0 0 0 6.6 6.6l2.2-2.2a1 1 0 0 1 1-.25 11.4 11.4 0 0 0 3.6.57 1 1 0 0 1 1 1V20a1 1 0 0 1-1 1A17 17 0 0 1 3 4a1 1 0 0 1 1-1h3.5a1 1 0 0 1 1 1c0 1.25.2 2.45.57 3.57a1 1 0 0 1-.25 1z"/>
      </svg>
    </li>
    <li class="contact-item">
      <span>www.esnorganized-example.com</span>
      <svg class="contact-icon" viewBox="0 0 24 24" aria-hidden="true">
        <circle cx="12" cy="12" r="10" fill="none" stroke="#1a7fd4" stroke-width="2.4"/>
        <path d="M2 12h20M12 2c3 3 3 17 0 20M12 2c-3 3-3 17 0 20" fill="none" stroke="#1a7fd4" stroke-width="2"/>
      </svg>
    </li>
    <li class="contact-item">
      <span>everyshelfsetneatly</span>
      <svg class="contact-icon" viewBox="0 0 24 24" aria-hidden="true">
        <rect x="2" y="2" width="20" height="20" rx="2" fill="#1a7fd4"/>
      </svg>
    </li>
  </ul>
</section>

</body>
</html>
```